Business Card Design Project

This is the first time we use our new logo. We need a business card that we can use both on our institutional corporate relationships and also that works for our staff that deals with consumers directly.

VELUNDA is a new company dedicated to empower consumers and to provide them with the best choices for specialized health care using the latest telemedicine technology (medicine at a distance via videoconference).

We want to print this cards in high quality materials and process. We will like designs that allow us to use UV spot varnish and other techniques that will differentiate us.

We are including Two different versions of Color logos. In addition we are including white over black background logos. Those can be used replacing the black for a color.

Please note this is the first time we will be creating any corporate materials with our new logo and colors.

Target Market(s)

34+ consumers of medium high and high socioeconomic levels.

Industry/Entity Type

Health

Requirements
Must have
• Our logo on its original colors
Should not have
• Any other graphical element or design that is not our logo

```html
<!DOCTYPE html>
<html lang="en">
<head>
<meta charset="utf-8">
<title>VELUNDA Business Card</title>
<link rel="stylesheet" href="https://fonts.googleapis.com/css2?family=Montserrat:wght@700&family=Arimo:wght@400;700&display=swap">
<style>
  :root {
    --page-bg: #e9e6e1;
    --card-dark: #141414;
    --card-mid: #262626;
    --brand-blue: #1d5a8c;
    --sky-blue: #4fb0e0;
    --teal: #1aa3a0;
    --panel-blue: #1b5f8d;
    --text-light: #f2f2f2;
  }
  * { box-sizing: border-box; margin: 0; padding: 0; }
  html, body { width: 1200px; height: 1057px; overflow: hidden; }
  body {
    background: var(--page-bg);
    font-family: "Arimo", Arial, sans-serif;
    position: relative;
  }
  .card {
    position: absolute;
    left: 180px;
    width: 840px;
    height: 480px;
    background: linear-gradient(135deg, var(--card-dark) 0%, var(--card-mid) 50%, var(--card-dark) 100%);
    overflow: hidden;
    box-shadow: 0 8px 24px rgba(0,0,0,0.25);
  }
  .card--front { top: 40px; }
  .card--back { top: 537px; }
  .card__waves { position: absolute; inset: 0; }
  .brand {
    position: absolute;
    display: flex;
    align-items: center;
    gap: 22px;
    color: var(--brand-blue);
    font-family: "Montserrat", Arial, sans-serif;
    font-weight: 700;
    letter-spacing: 0.08em;
  }
  .brand__dot {
    border-radius: 50%;
    background: var(--teal);
    flex: none;
  }
  .card--front .brand { left: 60px; top: 70px; font-size: 62px; }
  .card--front .brand__dot { width: 60px; height: 60px; }
  .person {
    position: absolute;
    left: 60px;
    top: 200px;
    font-family: "Montserrat", Arial, sans-serif;
    font-weight: 700;
    font-size: 28px;
    color: var(--sky-blue);
  }
  .person__title { font-family: "Arimo", Arial, sans-serif; font-weight: 400; font-size: 20px; }
  .contacts {
    position: absolute;
    left: 60px;
    top: 252px;
    list-style: none;
    color: var(--text-light);
    font-size: 21px;
    line-height: 32px;
  }
  .contacts li { display: flex; align-items: center; gap: 10px; }
  .contacts svg { width: 18px; height: 18px; flex: none; }
  .address {
    position: absolute;
    right: 28px;
    bottom: 28px;
    text-align: right;
    color: var(--text-light);
    font-size: 18px;
    line-height: 26px;
  }
  .card--back .brand { left: 160px; top: 150px; font-size: 84px; }
  .card--back .brand__dot { width: 80px; height: 80px; }
  .website {
    position: absolute;
    left: 0; right: 0;
    top: 310px;
    text-align: center;
    color: var(--sky-blue);
    font-size: 28px;
    letter-spacing: 0.3em;
  }
</style>
</head>
<body>
  <section class="card card--front">
    <svg class="card__waves" viewBox="0 0 840 480" aria-hidden="true">
      <path d="M400 480 Q640 380 840 140 L840 480 Z" fill="var(--panel-blue)"/>
      <path d="M0 430 C200 444 320 446 380 440 Q610 350 840 60 L840 84 Q620 364 390 456 C320 462 200 462 0 452 Z" fill="var(--teal)"/>
      <path d="M0 464 C200 472 330 472 392 464 Q630 366 840 106 L840 122 Q640 378 400 478 C330 486 200 486 0 480 Z" fill="var(--sky-blue)"/>
    </svg>
    <div class="brand"><span class="brand__dot"></span>VELUNDA</div>
    <p class="person">Your Name, <span class="person__title">Title</span></p>
    <ul class="contacts">
      <li><svg viewBox="0 0 20 20"><circle cx="10" cy="10" r="9" fill="none" stroke="var(--text-light)" stroke-width="2"/><path d="M7 5 L9 7 L8 9 L11 12 L13 11 L15 13 L13 15 C9 15 5 11 5 7 Z" fill="var(--text-light)"/></svg>012-345-6789</li>
      <li><svg viewBox="0 0 20 20"><circle cx="10" cy="10" r="9" fill="none" stroke="var(--text-light)" stroke-width="2"/><path d="M7 5 L9 7 L8 9 L11 12 L13 11 L15 13 L13 15 C9 15 5 11 5 7 Z" fill="var(--text-light)"/></svg>012-345-6789</li>
      <li><svg viewBox="0 0 20 20"><rect x="2" y="5" width="16" height="11" fill="none" stroke="var(--text-light)" stroke-width="2"/><path d="M2 5 L10 11 L18 5" fill="none" stroke="var(--text-light)" stroke-width="2"/></svg>name@velunda.com</li>
      <li><svg viewBox="0 0 20 20"><circle cx="10" cy="10" r="8" fill="none" stroke="var(--text-light)" stroke-width="2"/><path d="M2 10 H18 M10 2 C5 7 5 13 10 18 M10 2 C15 7 15 13 10 18" fill="none" stroke="var(--text-light)" stroke-width="1.5"/></svg>www.velunda.com</li>
    </ul>
    <p class="address">Street Name, City Name<br>State, City Zip Code</p>
  </section>

  <section class="card card--back">
    <div class="brand"><span class="brand__dot"></span>VELUNDA</div>
    <p class="website">www.velunda.com</p>
  </section>
</body>
</html>
```